Boundless Volt Product design

We need a bottle design for our product. Boundless Volt is a Gaming Nootropic made to increase Energy, Focus, Reaction time, and Clarity of an eSport gamer. It will be 40 servings a bottle. Currently, all the ingredients haven't been finalized so after the competition is over we will have to work with the designer to also make an ingredients label for the back of it. For the flavor, we will call it tundra mist.

The attachments included:. The velvet outlaws picture as a font style I like for the logo.
The Z CHARGE REFRESH PICTURE IS WHAT WE WANT OUR DESIGN to look like something similar a clean and simple design that stands out!

Z Charge bottle is what our biggest competitors product looks like. The boundless volt picture as the current logo we are using but can be changed.

Overall the pictures are just some references for what I could possibly want the design to look like however, I'm open to your designer's ideas and concepts you think would make for a cool looking Gaming Nootropic product bottle design. I appreciate everyone working on this and look forward to seeing your designs have a great day!

Target Market(s)

Gamers between the ages of 18-30

Industry/Entity Type

Health And Wellness

Requirements
Must have
• Boundless Volt logo, state that it is for energy, focus, reaction, and clarity. state 40 serivngs. state flavor.

```html
<!DOCTYPE html>
<html lang="en">
<head>
<meta charset="utf-8">
<title>Boundless Volt – Tundra Mist Label</title>
<link rel="stylesheet" href="https://fonts.googleapis.com/css2?family=Saira+Condensed:ital,wght@0,700;1,700&family=Open+Sans:wght@400&display=swap">
<style>
  :root {
    --page: #e9eaec;
    --label: #ffffff;
    --royal: #2f4f9e;
    --teal: #5cc4d0;
    --sky: #9fc6e8;
    --ink: #111418;
    --white: #ffffff;
    --legal: #dfe6f5;
  }
  * { margin: 0; padding: 0; box-sizing: border-box; }
  html, body { width: 1200px; height: 1024px; overflow: hidden; background: var(--page); }

  .label {
    position: absolute; left: 40px; top: 132px;
    width: 1120px; height: 760px;
    background: var(--label);
    overflow: hidden;
  }
  .texture-band {
    position: absolute; left: 0; top: 0; width: 100%; height: 100px;
    background: linear-gradient(180deg, #d6e6f5 0%, var(--sky) 55%, #eef5fb 100%);
    opacity: .8;
  }
  .servings-tab {
    position: absolute; left: 850px; top: 0; width: 110px; height: 370px;
    background: var(--royal);
    border-radius: 0 0 28px 28px;
    color: var(--white);
    font-family: "Saira Condensed", sans-serif; font-weight: 700;
    text-align: center;
  }
  .servings-tab .count { position: absolute; left: 0; right: 0; top: 226px; font-size: 70px; line-height: 1; }
  .servings-tab .unit { position: absolute; left: 0; right: 0; top: 306px; font-size: 26px; line-height: 1; }

  .brand {
    position: absolute; left: 0; width: 840px; top: 258px;
    display: flex; align-items: center; justify-content: center; gap: 22px;
  }
  .brand-mark { width: 34px; height: 34px; background: var(--teal); }
  .brand-name {
    font-family: "Saira Condensed", sans-serif; font-weight: 700;
    font-size: 92px; letter-spacing: 3px; line-height: 1; color: var(--ink);
  }
  .audience {
    position: absolute; left: 0; width: 840px; top: 432px;
    text-align: center;
    font-family: "Saira Condensed", sans-serif; font-style: italic; font-weight: 700;
    font-size: 60px; letter-spacing: 6px; line-height: 1; color: var(--royal);
  }

  .base-band {
    position: absolute; left: 0; top: 540px; width: 100%; height: 220px;
    background: var(--royal);
  }
  .stats {
    position: absolute; left: 250px; top: 540px; width: 400px; height: 90px;
    background: var(--white);
    clip-path: polygon(0 0, 100% 0, 96% 100%, 0 100%);
  }
  .stat {
    position: absolute; top: 0; width: 108px; height: 90px;
    background: var(--royal);
    clip-path: polygon(12% 0, 100% 0, 88% 100%, 0 100%);
    color: var(--white); text-align: center;
    font-family: "Saira Condensed", sans-serif; font-style: italic; font-weight: 700;
  }
  .stat:nth-child(1) { left: -8px; }
  .stat:nth-child(2) { left: 108px; }
  .stat:nth-child(3) { left: 224px; }
  .stat .zero { display: block; font-size: 56px; line-height: 1; margin-top: 6px; }
  .stat .what { display: block; font-size: 16px; letter-spacing: .5px; }
  .flavor {
    position: absolute; left: 660px; top: 550px;
    font-family: "Saira Condensed", sans-serif; font-style: italic; font-weight: 700;
    font-size: 64px; letter-spacing: 4px; color: var(--white); line-height: 1;
  }
  .benefits {
    position: absolute; left: 0; right: 0; top: 650px;
    text-align: center;
    font-family: "Saira Condensed", sans-serif; font-weight: 700;
    font-size: 46px; letter-spacing: 5px; color: var(--white); line-height: 1;
  }
  .legal {
    position: absolute; left: 0; right: 0; top: 712px;
    text-align: center;
    font-family: "Open Sans", sans-serif; font-size: 21px; color: var(--legal);
  }
</style>
</head>
<body>
  <main class="label">
    <div class="texture-band" role="img" aria-label="Light blue tiled pattern band"></div>

    <div class="servings-tab">
      <span class="count">40</span>
      <span class="unit">servings</span>
    </div>

    <div class="brand">
      <span class="brand-mark"></span>
      <span class="brand-name">BOUNDLESS VOLT</span>
    </div>

    <p class="audience">FOR E-SPORT GAMERS</p>

    <div class="base-band"></div>

    <div class="stats">
      <div class="stat"><span class="zero">0</span><span class="what">SUGAR</span></div>
      <div class="stat"><span class="zero">0</span><span class="what">CALORIES</span></div>
      <div class="stat"><span class="zero">0</span><span class="what">CAFFEINE</span></div>
    </div>

    <p class="flavor">TUNDRA MIST</p>
    <p class="benefits">ENERGY | FOCUS | REACTION | CLARITY</p>
    <p class="legal">Dietary Supplement | Net Weight 12 OZ (118g)</p>
  </main>
</body>
</html>
```